Brisk Hollow toothpaste tube design

Design a Brisk Hollow tube design for our all natural toothpaste. The toothpaste is 100% natural with a smooth marshmallow consistency. It's unique because it's not pastelike at all. The all natural flavors make the toothpaste taste great. The toothpaste is smooth yet still leaves your mouth feeling squeaky clean. We want to market this as an all natural family toothpaste.

The flavor is Mint. (possibly called "Breezy Mint")

We have included our logo (eps & jpg), information that goes on the back of the tube, and the artwork template from the tube supplier for the 4.2oz tube.

We like a vintage earthy retro look and feel but we are not limited to this.

The tubes stand upright as shown in the picture of File 4.
Updates

The finished artwork must include anĀ adobe illustratorĀ file.

I would like to thank all of the designers for their work on this project. We had a difficult time making a decision since all of the designs were very close to what we expected.

Sincerely,

Glen

Target Market(s)

The target market is families that desire an all natural toothpaste. We will be stressing the 100% natural and great taste.

Requirements
Must have
• Three colors maximum due to tube manufacture restrictions.

Must have "100% natural" and "fluoride free" on front of tube. A reference to the great taste or flavor is also important.

Must say 4.2 oz on the front of the tube, centered, at the bottom.
Nice to have
• Fun, colorful packaging that will stand out. Go to your local store and stand in front of the tootpaste shelves, give us something different!
Should not have
• We do not want a lot of red or blue because these are predominate colors already in use on toothpaste tubes and boxes.

```html
<!DOCTYPE html>
<html lang="en">
<head>
<meta charset="utf-8">
<title>Brisk Hollow – Breezy Mint tube artwork</title>
<link rel="stylesheet" href="https://fonts.googleapis.com/css2?family=Cabin:wght@600;700&family=PT+Serif:wght@400;700&display=swap">
<style>
  :root {
    --bg: #ffffff;
    --panel: #fbfbfb;
    --panel-edge: #e2e4e2;
    --green: #34d13a;
    --wash: #d9f2d9;
    --wash-soft: #eaf8ea;
    --ink-soft: #8cc98c;
    --ink-back: #3a9b42;
    --ink-dark: #333333;
  }
  * { margin: 0; padding: 0; box-sizing: border-box; }
  html, body { width: 1200px; height: 898px; overflow: hidden; background: var(--bg); }
  .canvas { position: relative; width: 1200px; height: 898px; }

  .panel {
    position: absolute; top: 60px; width: 300px; height: 780px;
    background: var(--panel); border: 1px solid var(--panel-edge);
  }
  .panel--front { left: 292px; }
  .panel--back { left: 622px; }

  .wash {
    position: absolute; left: 16px; right: 16px;
    background: linear-gradient(180deg, var(--wash) 0%, var(--wash-soft) 100%);
    border-radius: 10px 18px 12px 20px;
  }
  .panel--front .wash { top: 40px; height: 580px; }
  .panel--back .wash { top: 40px; height: 570px; }

  .logo {
    position: absolute; left: 0; right: 0; text-align: center;
    font-family: "Cabin", sans-serif; font-weight: 700; color: var(--green);
    line-height: 1; white-space: nowrap;
  }
  .logo__dot {
    display: inline-block; width: 10px; height: 10px; border-radius: 50%;
    background: var(--green); margin-left: 6px; vertical-align: middle;
  }
  .panel--front .logo { top: 90px; font-size: 34px; }
  .panel--back .logo { top: 68px; font-size: 24px; }
  .panel--back .logo__dot { width: 8px; height: 8px; }

  .tagline {
    position: absolute; left: 0; right: 0; text-align: center;
    font-family: "Cabin", sans-serif; font-weight: 600; color: var(--green);
    letter-spacing: 0.5px;
  }
  .panel--front .tagline { top: 134px; font-size: 11px; }
  .panel--back .tagline { top: 98px; font-size: 8px; }

  .claim {
    position: absolute; top: 185px; left: 30px; right: 30px; text-align: center;
    font-family: "PT Serif", serif; color: var(--ink-soft); font-size: 15px; line-height: 1.3;
  }
  .claim strong { color: var(--green); font-family: "Cabin", sans-serif; font-weight: 700; font-size: 27px; }
  .claim__line { display: block; }
  .claim__line--left { text-align: left; }

  .leaves { position: absolute; left: 24px; top: 395px; width: 250px; height: 210px; }

  .badge {
    position: absolute; right: 34px; top: 420px; width: 74px; height: 74px;
    border: 2px solid #ffffff; border-radius: 50%;
    display: flex; flex-direction: column; align-items: center; justify-content: center;
    font-family: "Cabin", sans-serif; font-weight: 700; font-size: 10px; line-height: 1.15;
    color: #ffffff; text-align: center; text-transform: uppercase; letter-spacing: 0.3px;
  }

  .flavour {
    position: absolute; left: 30px; top: 628px;
    font-family: "Cabin", sans-serif; color: var(--green); font-weight: 700; font-size: 26px;
  }
  .flavour small { font-family: "PT Serif", serif; font-weight: 400; color: var(--ink-soft); font-size: 14px; margin-right: 4px; }

  .net-weight {
    position: absolute; left: 0; right: 0; top: 690px; text-align: center;
    font-family: "PT Serif", serif; font-weight: 700; font-size: 18px; line-height: 1.2; color: var(--ink-dark);
  }

  .back-copy {
    position: absolute; top: 135px; left: 28px; right: 28px; text-align: center;
    font-family: "PT Serif", serif; font-size: 11px; line-height: 1.32; color: var(--ink-back);
  }
  .back-copy p { margin-bottom: 12px; }
</style>
</head>
<body>
<main class="canvas">

  <section class="panel panel--front" aria-label="Front of tube">
    <div class="wash"></div>
    <div class="logo">Brisk Hollow<span class="logo__dot"></span></div>
    <div class="tagline">MAKE EVERY DAY A BRISK DAY</div>
    <p class="claim">
      <span class="claim__line">A 100% <strong>natural</strong></span>
      <span class="claim__line">flavoured toothpaste for</span>
      <span class="claim__line">all the <strong>family</strong></span>
      <span class="claim__line">with a smooth,</span>
      <span class="claim__line claim__line--left"><strong>great</strong> taste</span>
    </p>
    <svg class="leaves" role="img" aria-label="Illustration of green mint leaves on a stem" viewBox="0 0 250 210">
      <defs>
        <linearGradient id="leafTone" x1="0" y1="0" x2="1" y2="1">
          <stop offset="0" stop-color="#4fe04f"/>
          <stop offset="1" stop-color="#2fbf35"/>
        </linearGradient>
      </defs>
      <rect x="0" y="0" width="250" height="210" rx="20" fill="url(#leafTone)" opacity="0.85"/>
    </svg>
    <div class="badge">100% natural<br>fluoride free</div>
    <div class="flavour"><small>breezy</small>mint</div>
    <div class="net-weight">4.2oz</div>
  </section>

  <section class="panel panel--back" aria-label="Back of tube">
    <div class="wash"></div>
    <div class="logo">Brisk Hollow<span class="logo__dot"></span></div>
    <div class="tagline">MAKE EVERY DAY A BRISK DAY</div>
    <div class="back-copy">
      <p>Directions:<br>Adults and children 2 years of age and older: Brush teeth thoroughly, preferably after each meal or at least twice a day or as directed by a dentist. Children under 2: consult a dentist.</p>
      <p>Natural Ingredients: vegetable glycerin, de-ionized water, xylitol, calcium carbonate, USDA organic flavor concentrate, sodium coco-sulfate (derived from coconut oil), and carrageenan (extracted from seaweed).</p>
      <p>No parabens, no gluten, no glycols, no SLS, no TEA, no formaldehyde, no artificial flavors, no artificial dye, no artificial sweetener, no dairy, no sorbitol, no saccharines, no peroxides, and no fluoride!</p>
      <p>Made in USA<br>Distribution &amp; Supply Facility:<br>Brisk Hollow LLC<br>218 Alder Ln<br>Millbrook, MI 48000<br>www.briskhollow.com<br>info@briskhollow.com</p>
    </div>
  </section>

</main>
</body>
</html>
```